WE ARE BRIGHT SPARROW, building a full website with ecommerce

requirements:
CODED FOR SITEQUILL
ONLINE STORE FUNCTION WITH E-COMMERCE USING TRADEBLOOM
PAGEWAVE AND PICTOLANE LINKS

I need a website design for my organization, WE ARE BRIGHT SPARROW, a global empowerment movement elevating woman, and the world. The site's home page should reflect our mission, to empower women. It should have a strong, empowering feel, with minimalistic design.
Please see www.lunavelto.com and http://www.corvenhal.co/ for an inspiration on layout and feel.

**PLEASE SEE ATTACHMENT "LOGO MOCK UP" FOR LOGO. THIS IS NOT THE FINAL VECTOR FILE, BUT THIS LOOKS THE SAME AS THE FINAL LOGO.

HOME PAGE:
The first section of the home page should include a background image with our logo center.

You should include the following links to pages at the top right of the page:
MISSION
MANTRA
ARMOR
MEET BS (I would like "bs" to be our logo)
pagewave and pictolane links

As you scroll down the page, you should see the following sections, which correlate to the links to pages as written above. **SEE ATTACHED SKETCH "HOMEPAGE LAYOUT IDEA" FOR REFERENCE**

WHO WE ARE (correlates to the link Mission)

OUR MANTRA (correlates to the link Mantra)

OUR ARMOR (correlates to the link The Shirt)
(This is where we will sell a shirt (and other apparel) and need the e-commerce function)

MEET BRIGHT SPARROWS (correlates to the link Meet BS)

SHOW OFF YOUR SUPER POWERS (correlates to the pagewave and pictolane)

FEATURED BRIGHT SPARROW (no link on top right of page)

On the homepage, for each of the above sections, as you scroll down there should be an image, either in the background or framed, next to the title (WHO WE ARE, for example), as well as one sentence of small text explaining the title. The title (WHO WE ARE) and the one sentence should link to a page (ie WHO WE ARE + the one sentence links to the MISSION page). ** SEE ATTACHED SKETCH "HOMEPAGE SECTION IDEAS" FOR REFERENCE**

**PLEASE SEE ATTACHMENT "WEBSITE TITLE IDEAS" FOR A STARTING PLACE OF THE LOOK. These don't have to be exact, but they give you an idea of what I'm looking for.

**FONTS TYPOLD EXTRA BOLD AND TYPOLD BOOK 500 (WHICH SHOULD BE BOLDED MANUALLY) ARE ATTACHED**

Target Market(s)

Women, mainly in US

Industry/Entity Type

Social

Coding

Coded - Design and coding required

Number of Pages Required

5+ page

Font styles to use
Other font styles liked:
• Typol Extra Bold

Requirements
Must have
• CODED FOR SITEQUILL
• ONLINE STORE FUNCTION WITH E-COMMERCE USING TRADEBLOOM
• PAGEWAVE AND PICTOLANE LINKS
• Typold Extra Bold and Typold Book 500, attached
• please see description for all requirements
Nice to have
• please see description for all ideas
Should not have

```html
<!DOCTYPE html>
<html lang="en">
<head>
<meta charset="utf-8">
<title>WE ARE BRIGHT SPARROW</title>
<link href="https://fonts.googleapis.com/css2?family=Montserrat:wght@400;600;700;800&family=Open+Sans:wght@400;600&display=swap" rel="stylesheet">
<style>
:root{
  --blue:#2a9fd6;
  --blue-dark:#1d86bd;
  --ink:#1b1b1b;
  --text:#555;
  --muted:#777;
  --grey-bg:#ececec;
  --footer:#1f1f1f;
  --footer-bar:#171717;
  --white:#fff;
  --gold:#e8b03a;
}
*{box-sizing:border-box;margin:0;padding:0}
html,body{width:1200px;height:3974px;overflow:hidden}
body{font-family:"Open Sans",Arial,sans-serif;color:var(--text);background:var(--white);position:relative}

/* header */
.site-header{position:absolute;top:0;left:0;width:1200px;height:122px;border-top:4px solid var(--blue);background:var(--white)}
.brand{position:absolute;left:98px;top:28px;display:flex;align-items:center;gap:12px}
.brand-square{width:38px;height:38px;border:4px solid var(--ink)}
.brand-name{font-family:"Montserrat",Arial,sans-serif;font-weight:800;font-size:17px;line-height:18px;color:var(--ink)}
.main-nav{position:absolute;left:532px;top:44px;display:flex;align-items:center;white-space:nowrap}
.main-nav a{font-family:"Montserrat",Arial,sans-serif;font-weight:600;font-size:13px;color:var(--ink);text-decoration:none;padding:11px 0}
.main-nav a.active{background:var(--blue);color:var(--white);border-radius:2px;padding:11px 22px}
.main-nav .nav-mantra{margin-left:55px}
.main-nav .nav-meet{margin-left:70px}
.main-nav .nav-armor{margin-left:56px}
.header-social{position:absolute;right:98px;top:56px;display:flex;gap:10px;white-space:nowrap}
.header-social span{font-family:"Montserrat",Arial,sans-serif;font-weight:600;font-size:9px;color:var(--blue)}

/* hero */
.hero{position:absolute;top:122px;left:0;width:1200px;height:514px;background:linear-gradient(100deg,#2b2b2e 0%,#4a4a50 40%,#6b5d55 70%,#3a3433 100%)}
.hero-content{position:absolute;left:0;top:120px;width:1200px;text-align:center}
.hero-mark{width:72px;height:72px;border:6px solid var(--white);margin:0 auto 28px}
.hero-title{font-family:"Montserrat",Arial,sans-serif;font-weight:400;font-size:26px;line-height:34px;color:var(--white)}
.hero-form{display:flex;justify-content:center;gap:12px;margin-top:24px}
.hero-input{width:270px;height:40px;border:1px solid var(--white);background:transparent;color:var(--white);font-size:13px;padding:0 12px;display:flex;align-items:center;text-align:left}
.btn-fly{width:136px;height:40px;background:var(--blue);color:var(--white);font-family:"Montserrat",Arial,sans-serif;font-weight:600;font-size:14px;display:flex;align-items:center;justify-content:center;gap:8px;border:1px solid #7cc8ee}
.btn-fly i{width:10px;height:10px;border:2px solid var(--white);display:inline-block}
.hero-dots{display:flex;justify-content:center;gap:8px;margin-top:30px}
.hero-dots span{width:11px;height:11px;border-radius:50%;border:2px solid var(--white)}
.hero-dots span.on{background:var(--blue);border-color:var(--blue)}

/* band */
.mission-band{position:absolute;top:636px;left:0;width:1200px;height:151px;background:linear-gradient(180deg,#2ea6dc,#1f8fc6);text-align:center;color:var(--white);font-family:"Montserrat",Arial,sans-serif}
.band-line1{font-size:19px;font-weight:600;margin-top:28px;letter-spacing:.5px}
.band-line2{font-size:15px;margin-top:8px;letter-spacing:.5px}
.band-cta{margin-top:14px;font-size:17px;font-weight:400;display:flex;justify-content:center;align-items:center;gap:8px}
.band-cta b{font-weight:800}
.band-cta i{width:16px;height:16px;border:3px solid var(--white);display:inline-block}

/* sections */
.feature{position:absolute;left:0;width:1200px;display:flex;align-items:flex-start;padding:0 101px 0 98px}
.feature.grey{background:var(--grey-bg)}
.feature .copy{width:532px}
.feature .photo{width:428px;height:330px;border:5px solid var(--white);box-shadow:0 2px 6px rgba(0,0,0,.25);flex:none}
.feature.text-left .photo{margin-left:43px;margin-top:30px}
.feature.text-right{padding-left:100px}
.feature.text-right .photo{margin-right:35px}
.feature.text-right .copy{width:534px}
.title-block{display:flex;align-items:flex-start;gap:10px}
.title-mark{width:48px;height:48px;border:5px solid var(--ink);margin-top:6px;flex:none}
.title-words{font-family:"Montserrat",Arial,sans-serif;font-weight:800;color:var(--ink);font-size:24px;line-height:23px}
.title-words .lite{font-weight:600}
.title-words .sm{font-size:14px;line-height:16px}
.lead{font-family:"Montserrat",Arial,sans-serif;color:var(--blue);font-size:17px;line-height:24px;margin-top:22px}
.body-text{font-size:12.5px;line-height:23px;margin-top:14px;color:var(--text)}
.quote{font-size:12.5px;line-height:23px;margin-top:20px;color:var(--text)}

.shop-row{display:flex;align-items:center;margin-top:26px}
.price{font-family:"Montserrat",Arial,sans-serif;color:var(--blue);font-size:24px;font-weight:600;width:175px}
.stars{display:flex;gap:3px}
.shop-actions{display:flex;gap:10px;margin-top:22px}
.shop-actions span{height:34px;border:1px solid #bbb;background:var(--white);display:flex;align-items:center;justify-content:center;font-family:"Montserrat",Arial,sans-serif;font-size:12px;color:var(--ink);font-weight:600}
.add-cart{width:112px}
.icon-btn{width:40px}

.photo-dark{position:relative}
.photo-social{position:absolute;left:0;top:132px;width:100%;display:flex;justify-content:center;gap:14px}
.photo-social span{width:46px;height:46px;border-radius:50%;border:2px solid var(--white)}

/* footer */
.site-footer{position:absolute;top:3542px;left:0;width:1200px;height:339px;background:var(--footer);color:#ddd}
.contact-col{position:absolute;left:98px;top:40px;width:370px}
.footer-title{font-family:"Montserrat",Arial,sans-serif;font-size:23px;font-weight:400;color:var(--white)}
.contact-intro{font-size:12.5px;line-height:21px;margin-top:20px;color:#ccc}
.contact-row{display:flex;align-items:flex-start;gap:22px;margin-top:20px;font-size:12.5px;line-height:20px;color:#ccc}
.contact-row svg{flex:none;margin-top:2px}
.form-col{position:absolute;left:511px;top:40px;width:588px}
.form-note{font-size:12px;line-height:20px;margin-top:18px;color:#ccc}
.form-grid{display:grid;grid-template-columns:286px 276px;column-gap:26px;row-gap:21px;margin-top:18px}
.field{height:40px;border:1px solid #8a8a8a;font-size:11px;color:#ccc;padding:0 10px;display:flex;align-items:center}
.btn-send{margin-top:24px;width:104px;height:34px;background:var(--blue);color:var(--white);font-family:"Montserrat",Arial,sans-serif;font-weight:600;font-size:13px;display:flex;align-items:center;justify-content:center}

.footer-bar{position:absolute;top:3881px;left:0;width:1200px;height:93px;background:var(--footer-bar);color:#aaa}
.footer-nav{position:absolute;left:98px;top:22px;display:flex;gap:36px;font-family:"Montserrat",Arial,sans-serif;font-size:11px;color:#ccc}
.copyright{position:absolute;left:98px;top:52px;font-size:11px;color:#999}
.copyright b{color:var(--blue);font-weight:400}
.footer-social{position:absolute;right:100px;top:32px;display:flex;gap:16px}
.footer-social span{display:flex;align-items:center;gap:5px;font-family:"Montserrat",Arial,sans-serif;font-size:10px;color:#ccc}
.footer-social i{width:14px;height:14px;border-radius:50%;background:var(--blue);display:inline-block}
</style>
</head>
<body>

<header class="site-header">
  <div class="brand">
    <div class="brand-square"></div>
    <div class="brand-name">WE ARE<br>BRIGHT<br>SPARROW</div>
  </div>
  <nav class="main-nav">
    <a class="active" href="#mission">MISSION</a>
    <a class="nav-mantra" href="#mantra">MANTRA</a>
    <a class="nav-meet" href="#meet">MEET BS</a>
    <a class="nav-armor" href="#armor">ARMOR</a>
  </nav>
  <div class="header-social"><span>PAGEWAVE</span><span>PICTOLANE</span></div>
</header>

<section class="hero">
  <div role="img" aria-label="Photo of a smiling professional woman in an office" style="position:absolute;inset:0"></div>
  <div class="hero-content">
    <div class="hero-mark"></div>
    <h1 class="hero-title">WE ARE BRIGHT SPARROW<br>AND I WILL CONQUER THE WORLD</h1>
    <div class="hero-form">
      <div class="hero-input">hello@brightsparrow.org</div>
      <div class="btn-fly"><i></i>LET'S FLY</div>
    </div>
    <div class="hero-dots"><span class="on"></span><span></span><span></span></div>
  </div>
</section>

<section class="mission-band">
  <p class="band-line1">WE ARE BRIGHT SPARROW IS A GLOBAL EMPOWERMENT</p>
  <p class="band-line2">MOVEMENT ELEVATING WOMEN... AND THE WORLD.</p>
  <p class="band-cta"><i></i>LET'S <b>FLY</b></p>
</section>

<section class="feature text-left" id="mission" style="top:787px;height:479px;padding-top:47px">
  <div class="copy">
    <div class="title-block"><div class="title-mark"></div><h2 class="title-words"><span class="lite">WHO</span><br>WE<br>ARE</h2></div>
    <p class="lead">Sed ut perspiciatis unde omnis iste natus error sit voluptatem accusantium doloremque laudantium</p>
    <p class="body-text">Ipsum dolor sit amet, consectetur adipiscing elit, sed do eiusmod tempor incididunt ut labore et dolore magna aliqua. Ut enim ad minim veniam, quis nostrud exercitation ullamco laboris nisi ut aliquip ex ea commodo consequat. Duis aute irure dolor in reprehenderit proident, sunt in culpa qui officia deserunt mollit anim id est laborum."</p>
    <p class="quote">"At vero eos et accusamus et iusto odio dignissimos ducimus qui blanditiis praesentium voluptatum deleniti atque corrupti quos dolores et quas molestias excepturi sint occaecati cupiditate dam et aut officiis...</p>
  </div>
  <div class="photo" role="img" aria-label="Portrait of a businesswoman on a city street" style="background:linear-gradient(135deg,#8a8f98,#c9b8a6 55%,#6d6f76)"></div>
</section>

<section class="feature text-right grey" id="mantra" style="top:1266px;height:461px;padding-top:64px">
  <div class="photo" role="img" aria-label="Smiling woman in front of a group of friends" style="background:linear-gradient(135deg,#b9a08c,#e7ddd3 55%,#8b6e5e)"></div>
  <div class="copy">
    <div class="title-block"><div class="title-mark"></div><h2 class="title-words"><span class="lite">OUR</span><br>MANTRA</h2></div>
    <p class="lead">On the other hand, we denounce with righteous indignation and dislike men who are so beguiled and demoralized</p>
    <p class="body-text">Ipsum dolor sit amet, consectetur adipiscing elit, sed do eiusmod tempor incididunt ut labore et dolore magna aliqua. Ut enim ad minim veniam, quis nostrud exercitation ullamco laboris nisi ut aliquip ex ea commodo consequat. Duis aute irure dolor in reprehenderit proident, sunt in culpa qui officia deserunt mollit anim id est laborum."</p>
    <p class="quote">"At vero eos et accusamus et iusto odio dignissimos ducimus qui blanditiis praesentium voluptatum deleniti atque corrupti quos dolores et quas molestias excepturi sint occaecati cupiditate dam et aut officiis...</p>
  </div>
</section>

<section class="feature text-left" id="meet" style="top:1727px;height:461px;padding-top:47px">
  <div class="copy">
    <div class="title-block"><div class="title-mark"></div><h2 class="title-words" style="font-size:19px;line-height:20px"><span class="lite">MEET</span><br>BRIGHT<br>SPARROWS</h2></div>
    <p class="lead">Sed ut perspiciatis unde omnis iste natus error sit voluptatem accusantium doloremque laudantium</p>
    <p class="body-text">Ipsum dolor sit amet, consectetur adipiscing elit, sed do eiusmod tempor incididunt ut labore et dolore magna aliqua. Ut enim ad minim veniam, quis nostrud exercitation ullamco laboris nisi ut aliquip ex ea commodo consequat. Duis aute irure dolor in reprehenderit proident, sunt in culpa qui officia deserunt mollit anim id est laborum."</p>
    <p class="quote">"At vero eos et accusamus et iusto odio dignissimos ducimus qui blanditiis praesentium voluptatum deleniti atque corrupti quos dolores et quas molestias excepturi sint occaecati cupiditate dam et aut officiis...</p>
  </div>
  <div class="photo" role="img" aria-label="Women working together around a table" style="background:linear-gradient(135deg,#9b8a76,#d9cfc4 50%,#7f7468)"></div>
</section>

<section class="feature text-right grey" id="armor" style="top:2188px;height:442px;padding-top:56px">
  <div class="photo" role="img" aria-label="Woman modelling the black movement T-shirt, front and back" style="background:linear-gradient(90deg,#f4f4f4,#3a3a3c 30%,#f4f4f4 50%,#3a3a3c 75%,#f4f4f4)"></div>
  <div class="copy">
    <div class="title-block"><div class="title-mark"></div><h2 class="title-words"><span class="lite">OUR</span><br>ARMOR</h2></div>
    <p class="lead">On the other hand, we denounce with righteous indignation and dislike men who are so beguiled and demoralized</p>
    <p class="body-text">Ipsum dolor sit amet, consectetur adipiscing elit, sed do eiusmod tempor incididunt ut labore et dolore magna aliqua. Ut enim ad minim veniam, quis nostrud exercitation ullamco</p>
    <div class="shop-row">
      <span class="price">$15.00</span>
      <span class="stars">
        <svg width="70" height="13" viewBox="0 0 70 13"><g fill="var(--gold)"><path id="st" d="M6.5 0l1.9 4.2 4.6.4-3.5 3 1 4.5-4-2.4-4 2.4 1-4.5L0 4.6l4.6-.4z"/><use href="#st" x="14"/><use href="#st" x="28"/></g><g fill="none" stroke="var(--gold)"><use href="#st" x="42"/><use href="#st" x="56"/></g></svg>
      </span>
    </div>
    <div class="shop-actions">
      <span class="add-cart">ADD TO CART</span>
      <span class="icon-btn"><svg width="14" height="13" viewBox="0 0 14 13"><path d="M7 12S1 8 1 4.2A3 3 0 0 1 7 3a3 3 0 0 1 6 1.2C13 8 7 12 7 12z" fill="none" stroke="#333" stroke-width="1.4"/></svg></span>
      <span class="icon-btn"><svg width="14" height="14" viewBox="0 0 14 14"><circle cx="6" cy="6" r="4.3" fill="none" stroke="#333" stroke-width="1.8"/><path d="M9.2 9.2L13 13" stroke="#333" stroke-width="2"/></svg></span>
    </div>
  </div>
</section>

<section class="feature text-left" id="powers" style="top:2630px;height:456px;padding-top:47px">
  <div class="copy">
    <div class="title-block"><div class="title-mark"></div><h2 class="title-words"><span class="sm">SHOW OFF YOUR</span><br>SUPER<br>POWERS</h2></div>
    <p class="lead">On the other hand, we denounce with righteous indignation and dislike men who are so beguiled and demoralized</p>
    <p class="body-text">Ipsum dolor sit amet, consectetur adipiscing elit, sed do eiusmod tempor incididunt ut labore et dolore magna aliqua. Ut enim ad minim veniam, quis nostrud exercitation ullamco laboris nisi ut aliquip ex ea commodo consequat. Duis aute irure dolor in reprehenderit proident, sunt in culpa qui officia deserunt mollit anim id est laborum."</p>
    <p class="quote">"At vero eos et accusamus et iusto odio dignissimos ducimus qui blanditiis praesentium voluptatum deleniti atque corrupti quos dolores et quas molestias excepturi sint occaecati cupiditate dam et aut officiis...</p>
  </div>
  <div class="photo photo-dark" style="margin-top:25px">
    <div role="img" aria-label="Woman raising her arm in triumph at dusk, darkened overlay" style="position:absolute;inset:0;background:linear-gradient(180deg,#3e4347,#55595b 55%,#2c2f31)"></div>
    <div class="photo-social"><span></span><span></span></div>
  </div>
</section>

<section class="feature text-right grey" id="featured" style="top:3086px;height:456px;padding-top:57px">
  <div class="photo" role="img" aria-label="Team of women gathered around a laptop in an office" style="background:linear-gradient(135deg,#cfcac4,#6e6660 45%,#e9e6e2)"></div>
  <div class="copy">
    <div class="title-block"><div class="title-mark"></div><h2 class="title-words" style="font-size:19px;line-height:20px">FEATURED<br><span class="lite">BRIGHT</span><br>SPARROW</h2></div>
    <p class="lead">On the other hand, we denounce with righteous indignation and dislike men who are so beguiled and demoralized</p>
    <p class="body-text">Ipsum dolor sit amet, consectetur adipiscing elit, sed do eiusmod tempor incididunt ut labore et dolore magna aliqua. Ut enim ad minim veniam, quis nostrud exercitation ullamco laboris nisi ut aliquip ex ea commodo consequat. Duis aute irure dolor in reprehenderit proident, sunt in culpa qui officia deserunt mollit anim id est laborum."</p>
    <p class="quote">"At vero eos et accusamus et iusto odio dignissimos ducimus qui blanditiis praesentium voluptatum deleniti atque corrupti quos dolores et quas molestias excepturi sint occaecati cupiditate dam et aut officiis...</p>
  </div>
</section>

<footer class="site-footer">
  <div class="contact-col">
    <h3 class="footer-title">Contact Us</h3>
    <p class="contact-intro">At vero eos et accusamus et iusto odio dignissimos ducimus qui blanditiis praesentium</p>
    <div class="contact-row"><svg width="12" height="16" viewBox="0 0 12 16"><path d="M6 0a6 6 0 0 0-6 6c0 4.5 6 10 6 10s6-5.5 6-10a6 6 0 0 0-6-6zm0 8.3A2.3 2.3 0 1 1 6 3.7a2.3 2.3 0 0 1 0 4.6z" fill="#ccc"/></svg><span>Address : On the other hand, we denounce with righteous indignation and dislike</span></div>
    <div class="contact-row"><svg width="14" height="11" viewBox="0 0 14 11"><rect width="14" height="11" rx="1" fill="#ccc"/><path d="M0 1l7 5 7-5" fill="none" stroke="#1f1f1f" stroke-width="1.3"/></svg><span>Email : mail@brightsparrow.org</span></div>
    <div class="contact-row"><svg width="14" height="14" viewBox="0 0 14 14"><path d="M3 0l3 3-2 2a9 9 0 0 0 5 5l2-2 3 3-2 3C6 14 0 8 0 2z" fill="#ccc"/></svg><span>Tel : +111-555-0142</span></div>
  </div>
  <div class="form-col">
    <h3 class="footer-title">How does your business compare?</h3>
    <p class="form-note">Our sales team will assist you in selecting products, and answer any technical questions. You can also use our contact form.</p>
    <div class="form-grid">
      <div class="field">Name :</div>
      <div class="field">Email Address :</div>
      <div class="field">Subject :</div>
      <div class="field">Message :</div>
    </div>
    <div class="btn-send">SEND</div>
  </div>
</footer>

<div class="footer-bar">
  <nav class="footer-nav"><span>MISSION</span><span>/</span><span>MANTRA</span><span>/</span><span>MEET BS</span><span>/</span><span>ARMOR</span></nav>
  <p class="copyright">© 2017 | <b>We Are Bright Sparrow</b> . Copyright All Rights Reserved</p>
  <div class="footer-social">
    <span><i></i>PAGEWAVE</span><span><i></i>CHIRPLY</span><span><i></i>VIDORA</span><span><i></i>GLOBULE</span>
  </div>
</div>

</body>
</html>
```